The Lanterns of Quiet Harbour - 12-Week Orchard Ledger

I am finishing a book that is designed to be super hands on. It steps he reader through a 90 day roadmap - as a pick up, put down action diary style piece. The foundational idea is to speak about the Lanterns of Quiet Harbour. With a cost of living crisis this is designed to create action and understanding. I am looking for a cover for the ebook that will blow away the competitors in the category. I want it to be bright, attractive and leap off the velluma page - appeal to a wide audience. I have pasted in a file with the best selling books in the category so you can see what's working.

```html
<!DOCTYPE html>
<html lang="en">
<head>
<meta charset="utf-8">
<title>The Lanterns of Quiet Harbour – Ebook Cover</title>
<link rel="stylesheet" href="https://fonts.googleapis.com/css2?family=League+Gothic&family=Montserrat:wght@500&display=swap">
<style>
  :root {
    --page-bg: #e9eaed;
    --navy-deep: #15294a;
    --navy: #1d365d;
    --navy-light: #27436f;
    --navy-ghost: rgba(58, 92, 145, 0.35);
    --gold: #e0bd78;
    --gold-soft: rgba(224, 189, 120, 0.22);
    --white: #ffffff;
  }
  * { box-sizing: border-box; margin: 0; padding: 0; }
  html, body {
    width: 1200px;
    height: 835px;
    overflow: hidden;
    background: var(--page-bg);
  }
  .canvas {
    position: relative;
    width: 1200px;
    height: 835px;
  }
  .cover {
    position: absolute;
    left: 335px;
    top: 20px;
    width: 530px;
    height: 795px;
    overflow: hidden;
    background:
      radial-gradient(ellipse at 30% 25%, var(--navy-light) 0%, transparent 60%),
      linear-gradient(180deg, var(--navy) 0%, var(--navy-deep) 100%);
  }
  .ghost-word {
    position: absolute;
    top: 28px;
    width: 68px;
    height: 740px;
    overflow: hidden;
    font-family: "League Gothic", sans-serif;
    font-size: 92px;
    line-height: 68px;
    color: var(--navy-ghost);
    writing-mode: vertical-rl;
    letter-spacing: 2px;
    white-space: nowrap;
  }
  .ghost-word--one { left: 286px; }
  .ghost-word--two { left: 356px; }
  .ghost-word--three { left: 428px; }
  .cage-art {
    position: absolute;
    left: 234px;
    top: 252px;
    width: 258px;
    height: 466px;
    border-radius: 130px 130px 20px 20px;
    background: radial-gradient(ellipse at 50% 35%, var(--gold-soft) 0%, rgba(224, 189, 120, 0.06) 70%, transparent 100%);
  }
  .title {
    position: absolute;
    left: 53px;
    top: 106px;
    font-family: "League Gothic", sans-serif;
    font-weight: 400;
    font-size: 100px;
    line-height: 88px;
    color: var(--white);
    text-transform: uppercase;
  }
  .title__line { display: block; }
  .title__line--accent { color: var(--gold); }
  .title__hero {
    position: absolute;
    font-family: "League Gothic", sans-serif;
    font-weight: 400;
    font-size: 152px;
    line-height: 0.8;
    color: var(--white);
    text-transform: uppercase;
    transform: skewX(-9deg);
    white-space: nowrap;
  }
  .title__hero--top { left: 280px; top: 356px; }
  .title__hero--bottom { left: 262px; top: 478px; }
  .author {
    position: absolute;
    left: 53px;
    top: 712px;
    font-family: "Montserrat", sans-serif;
    font-weight: 500;
    font-size: 26px;
    color: var(--white);
  }
</style>
</head>
<body>
  <main class="canvas">
    <section class="cover" aria-label="Ebook cover: A 12-Week Ledger Toward Harbour Lanterns by John Doe">
      <span class="ghost-word ghost-word--one" aria-hidden="true">LANTERNS</span>
      <span class="ghost-word ghost-word--two" aria-hidden="true">LANTERNS</span>
      <span class="ghost-word ghost-word--three" aria-hidden="true">LANTERNS</span>

      <div class="cage-art" role="img" aria-label="Gold line illustration of an open birdcage bursting apart"></div>

      <h1 class="title">
        <span class="title__line">A 12-Week</span>
        <span class="title__line">Ledger</span>
        <span class="title__line">Toward</span>
        <span class="title__line title__line--accent">Harbour</span>
      </h1>
      <span class="title__hero title__hero--top">Lant</span>
      <span class="title__hero title__hero--bottom">erns</span>

      <p class="author">John Doe</p>
    </section>
  </main>
</body>
</html>
```